RWT Fittings Ltd Business Cards

We need a business card with our business logo. We provide window and door installations on high-rises in west coast British Colombia, Canada.

I would like my business information and details on one side of the card, and the other side the company name with logo

Target Market(s)

General Contractors

Industry/Entity Type

Construction

Contact Information for Business Card

one side i want my company name and logo in the dark theme logo that i provided

Requirements
Must have
• Marco Peltieri, 16045518293, RWTFittings@mailbox-demo.com, 1407-5194 Linden Row Burnaby BC, V5H 2K9, Owner & Manager

```html
<!DOCTYPE html>
<html lang="en">
<head>
<meta charset="utf-8">
<title>RWT Fittings Ltd — Business Cards</title>
<link rel="stylesheet" href="https://fonts.googleapis.com/css2?family=Montserrat:wght@600;700;800&family=Roboto:wght@400;500&display=swap">
<style>
  :root {
    --stage: #232323;
    --brand-blue: #29a9e1;
    --ink-black: #161617;
    --card-dark: #1f2023;
    --band-mid: #1a1b1e;
    --band-deep: #151618;
    --name-grey: #9a9a9c;
    --text-light: #f2f2f2;
  }
  * { box-sizing: border-box; margin: 0; padding: 0; }
  html, body {
    width: 1200px; height: 780px; overflow: hidden;
    background: var(--stage);
  }
  .stage {
    position: relative; width: 1200px; height: 780px;
  }
  .card {
    position: absolute; top: 70px;
    width: 400px; height: 640px;
    border-radius: 24px; overflow: hidden;
    box-shadow: 0 10px 28px rgba(0,0,0,0.55);
  }

  /* Logo side */
  .card--brand {
    left: 150px; background: var(--brand-blue);
  }
  .brand-mark {
    position: absolute; left: 50%; top: 50%;
    transform: translate(-50%, -50%) rotate(-90deg);
    display: flex; align-items: center; gap: 22px;
    white-space: nowrap;
  }
  .brand-mark__square {
    width: 54px; height: 54px; background: var(--ink-black);
  }
  .brand-mark__name {
    font-family: "Montserrat", sans-serif; font-weight: 800;
    font-size: 50px; color: var(--ink-black); letter-spacing: 0.5px;
  }

  /* Details side */
  .card--details {
    left: 650px; background: var(--card-dark);
  }
  .card__bands { position: absolute; inset: 0; }
  .details-logo {
    position: absolute; top: 70px; left: 0; right: 0;
    display: flex; justify-content: center; align-items: center; gap: 12px;
  }
  .details-logo__square { width: 26px; height: 26px; background: var(--brand-blue); }
  .details-logo__name {
    font-family: "Montserrat", sans-serif; font-weight: 800;
    font-size: 28px; color: var(--brand-blue);
  }
  .person {
    position: absolute; top: 268px; left: 0; right: 0; text-align: center;
  }
  .person__name {
    font-family: "Montserrat", sans-serif; font-weight: 800; font-size: 34px;
  }
  .person__first { color: var(--brand-blue); }
  .person__last { color: var(--name-grey); }
  .person__role {
    font-family: "Montserrat", sans-serif; font-weight: 700; font-size: 15px;
    color: var(--text-light); margin-top: 2px;
  }
  .contact-icons {
    display: flex; justify-content: center; gap: 12px; margin-top: 12px;
  }
  .icon-dot {
    width: 28px; height: 28px; border-radius: 50%;
    background: var(--brand-blue); display: flex; align-items: center; justify-content: center;
  }
  .icon-dot svg { width: 15px; height: 15px; }
  .contact-line {
    font-family: "Roboto", sans-serif; font-size: 16px; color: var(--text-light);
    margin-top: 8px; letter-spacing: 0.3px;
  }
  .contact-line + .contact-line { margin-top: 4px; }
  .address {
    position: absolute; top: 520px; left: 0; right: 0; text-align: center;
    font-family: "Roboto", sans-serif; font-size: 16px; color: var(--text-light);
    line-height: 1.35;
  }
  .address .icon-dot { margin: 0 auto 10px; }
</style>
</head>
<body>
<main class="stage">

  <section class="card card--brand" aria-label="Card front: company name">
    <div class="brand-mark">
      <span class="brand-mark__square"></span>
      <span class="brand-mark__name">RWT Fittings Ltd</span>
    </div>
  </section>

  <section class="card card--details" aria-label="Card back: contact details">
    <svg class="card__bands" viewBox="0 0 400 640" preserveAspectRatio="none" aria-hidden="true">
      <path d="M0 455 C 120 520, 300 500, 400 415 L400 640 L0 640 Z" fill="var(--band-mid)"/>
      <path d="M0 640 L0 610 C 60 560, 130 480, 400 470 L400 640 Z" fill="var(--band-deep)"/>
    </svg>

    <div class="details-logo">
      <span class="details-logo__square"></span>
      <span class="details-logo__name">RWT Fittings Ltd</span>
    </div>

    <div class="person">
      <p class="person__name"><span class="person__first">Marco</span> <span class="person__last">Peltieri</span></p>
      <p class="person__role">Owner &amp; Manager</p>
      <div class="contact-icons">
        <span class="icon-dot">
          <svg viewBox="0 0 24 24" aria-hidden="true"><path fill="#fff" d="M6.6 10.8a15.1 15.1 0 0 0 6.6 6.6l2.2-2.2a1 1 0 0 1 1-.25 11.4 11.4 0 0 0 3.6.57 1 1 0 0 1 1 1V20a1 1 0 0 1-1 1A17 17 0 0 1 3 4a1 1 0 0 1 1-1h3.5a1 1 0 0 1 1 1c0 1.25.2 2.45.57 3.57a1 1 0 0 1-.25 1z"/></svg>
        </span>
        <span class="icon-dot">
          <svg viewBox="0 0 24 24" aria-hidden="true"><path fill="#fff" d="M3 5h18a1 1 0 0 1 1 1v12a1 1 0 0 1-1 1H3a1 1 0 0 1-1-1V6a1 1 0 0 1 1-1zm1 2.2V17h16V7.2l-8 5.3z M4.6 7l7.4 4.9L19.4 7z"/></svg>
        </span>
      </div>
      <p class="contact-line">1604 551 8293</p>
      <p class="contact-line">RWTFittings@mailbox-demo.com</p>
    </div>

    <div class="address">
      <span class="icon-dot">
        <svg viewBox="0 0 24 24" aria-hidden="true"><path fill="#fff" d="M12 2a7 7 0 0 0-7 7c0 5.2 7 13 7 13s7-7.8 7-13a7 7 0 0 0-7-7zm0 9.5A2.5 2.5 0 1 1 12 6.5a2.5 2.5 0 0 1 0 5z"/></svg>
      </span>
      <p>1407-5194 Linden Row</p>
      <p>Burnaby BC, V5H 2K9</p>
    </div>
  </section>

</main>
</body>
</html>
```